Tovrenna Capital LLC

Need Professional Business cards for New Investment Fund

Target Market(s)

High Quality investors

Industry/Entity Type

Financial

Contact Information for Business Card

Phone Number +1 555 284 6190
Name Lukas Varenko
Title Fund Manager
email lv@FundTovrenna.com
Website www.FundTovrenna.com

Colors

Designer to choose colors to be used in the design.

Requirements
Must have
• Must have our Logo and all of the above. Must be made so lettering and loge can be raised

```html
<!DOCTYPE html>
<html lang="en">
<head>
<meta charset="utf-8">
<title>Tovrenna Capital LLC — Business Card</title>
<link rel="stylesheet" href="https://fonts.googleapis.com/css2?family=Montserrat:wght@300;400;600&display=swap">
<style>
  :root {
    --bg: #141414;
    --card: #2e2e2f;
    --card-back: #2a2a2b;
    --pattern-light: #363637;
    --green: #3ee01f;
    --white: #f4f4f4;
    --rule: #bdbdbd;
  }
  * { margin: 0; padding: 0; box-sizing: border-box; }
  html, body {
    width: 1200px; height: 900px; overflow: hidden;
    background: var(--bg);
    font-family: "Montserrat", sans-serif;
  }
  .stage {
    width: 1200px; height: 900px;
    display: flex; align-items: center; justify-content: center; gap: 90px;
  }
  .card {
    width: 340px; height: 520px;
    border-radius: 26px;
    position: relative;
    overflow: hidden;
  }
  .card-front {
    background: var(--card);
    display: flex; flex-direction: column; align-items: center;
    color: var(--white);
    text-align: center;
  }
  .wordmark {
    display: flex; align-items: center; gap: 10px;
    color: var(--white);
    font-weight: 600;
    letter-spacing: 0.1em;
    white-space: nowrap;
  }
  .wordmark-mark { background: var(--green); display: block; flex: none; }
  .card-front .wordmark { margin-top: 120px; font-size: 26px; }
  .card-front .wordmark-mark { width: 18px; height: 18px; }
  .contact { margin-top: auto; margin-bottom: 46px; display: flex; flex-direction: column; align-items: center; }
  .person-name {
    color: var(--green); font-weight: 600; font-size: 20px; letter-spacing: 0.06em;
    text-transform: uppercase;
  }
  .person-title { font-weight: 300; font-size: 15px; margin-top: 2px; letter-spacing: 0.03em; }
  .divider { width: 190px; height: 1px; background: var(--rule); }
  .divider-top { margin-top: 10px; }
  .divider-bottom { margin-bottom: 10px; }
  .icons { display: flex; gap: 5px; margin: 7px 0; }
  .icon { width: 22px; height: 22px; display: block; }
  .contact-line { font-weight: 400; font-size: 15px; line-height: 1.45; letter-spacing: 0.01em; }

  .card-back { background: var(--card-back); }
  .back-texture {
    position: absolute; inset: 0;
    background: linear-gradient(155deg, var(--pattern-light) 0%, var(--card-back) 60%, var(--pattern-light) 100%);
  }
  .card-back .wordmark {
    position: absolute; left: 50%; top: 50%; transform: translate(-50%, -50%);
    font-size: 18px;
  }
  .card-back .wordmark-mark { width: 12px; height: 12px; }
</style>
</head>
<body>
<main class="stage">
  <section class="card card-front" aria-label="Card front">
    <div class="wordmark"><span class="wordmark-mark"></span>TOVRENNA</div>
    <div class="contact">
      <p class="person-name">Lukas Varenko</p>
      <p class="person-title">Fund Manager</p>
      <div class="divider divider-top"></div>
      <div class="icons">
        <svg class="icon" viewBox="0 0 22 22" aria-label="Phone">
          <circle cx="11" cy="11" r="11" fill="var(--green)"/>
          <path d="M7.5 6.5c.6-.6 1.3-.5 1.6 0l1 1.6c.3.5.1 1-.3 1.3l-.6.4c.5 1.2 1.5 2.2 2.7 2.7l.4-.6c.3-.4.8-.6 1.3-.3l1.6 1c.5.3.6 1 0 1.6-.8.8-2 1-3.2.4-2-1-3.6-2.6-4.6-4.6-.6-1.2-.4-2.4.1-3.5z" fill="var(--card)"/>
        </svg>
        <svg class="icon" viewBox="0 0 22 22" aria-label="Email">
          <circle cx="11" cy="11" r="11" fill="var(--green)"/>
          <rect x="5.5" y="7.5" width="11" height="7.5" rx="1" fill="var(--card)"/>
          <path d="M5.8 8l5.2 4 5.2-4" stroke="var(--green)" stroke-width="1" fill="none"/>
        </svg>
        <svg class="icon" viewBox="0 0 22 22" aria-label="Website">
          <circle cx="11" cy="11" r="11" fill="var(--green)"/>
          <g stroke="var(--card)" stroke-width="1.3" fill="none">
            <circle cx="11" cy="11" r="5.5"/>
            <ellipse cx="11" cy="11" rx="2.3" ry="5.5"/>
            <path d="M5.5 11h11"/>
          </g>
        </svg>
      </div>
      <div class="divider divider-bottom"></div>
      <p class="contact-line">+1 555 284 6190</p>
      <p class="contact-line">lv@FundTovrenna.com</p>
      <p class="contact-line">www.FundTovrenna.com</p>
    </div>
  </section>

  <section class="card card-back" aria-label="Card back">
    <div class="back-texture" role="img" aria-label="Tone-on-tone brand pattern across the card back"></div>
    <div class="wordmark"><span class="wordmark-mark"></span>TOVRENNA</div>
  </section>
</main>
</body>
</html>
```